Business Card Design

I already have a company logo for my company. I have a logo for the manufacturer we represent. I want a professional business card design.

```html
<!DOCTYPE html>
<html lang="en">
<head>
<meta charset="utf-8">
<title>Beacon Hazard Co. – Business Card</title>
<link rel="stylesheet" href="https://fonts.googleapis.com/css2?family=Open+Sans:wght@400;600;700;800&display=swap">
<style>
  :root {
    --stage: #1d1d1f;
    --card: #222225;
    --card-back-a: #18181a;
    --card-back-b: #2a2a2d;
    --red: #e31e24;
    --gold: #c8962e;
    --white: #f4f4f4;
  }
  * { box-sizing: border-box; margin: 0; padding: 0; }
  html, body { width: 1200px; height: 780px; overflow: hidden; }
  body {
    background: var(--stage);
    font-family: "Open Sans", Arial, sans-serif;
    position: relative;
  }
  .card {
    position: absolute;
    top: 240px;
    width: 525px;
    height: 300px;
    border-radius: 18px;
    overflow: hidden;
    box-shadow: 0 18px 40px rgba(0,0,0,.45);
  }
  .card--front { left: 50px; background: var(--card); }
  .card--back { left: 625px; }

  /* Front */
  .brand {
    position: absolute;
    left: 38px;
    top: 92px;
    width: 200px;
    display: flex;
    align-items: center;
    gap: 10px;
  }
  .brand__dot {
    width: 22px; height: 22px;
    border-radius: 50%;
    background: var(--red);
    flex: none;
  }
  .brand__name {
    font-weight: 800;
    font-size: 21px;
    line-height: 1.1;
    color: var(--white);
    text-transform: uppercase;
    letter-spacing: .5px;
  }
  .divider {
    position: absolute;
    left: 0; top: 0;
    width: 525px; height: 256px;
  }
  .identity {
    position: absolute;
    left: 318px;
    top: 52px;
  }
  .identity__name {
    font-weight: 700;
    font-size: 30px;
    line-height: 1;
    white-space: nowrap;
  }
  .identity__first { color: var(--red); }
  .identity__last { color: var(--gold); }
  .identity__role {
    margin-top: 6px;
    font-size: 14px;
    color: var(--white);
  }
  .contacts {
    position: absolute;
    left: 306px;
    top: 136px;
    list-style: none;
  }
  .contacts__item {
    display: flex;
    align-items: center;
    gap: 9px;
    font-size: 14.5px;
    color: var(--white);
    line-height: 1;
    margin-bottom: 10px;
    white-space: nowrap;
  }
  .contacts__icon { width: 13px; height: 13px; flex: none; fill: var(--red); }
  .address-band {
    position: absolute;
    left: 0; bottom: 0;
    width: 100%;
    height: 44px;
    background: var(--red);
    color: var(--white);
    font-size: 14.5px;
    display: flex;
    align-items: center;
    padding-left: 40px;
  }

  /* Back */
  .back-pattern {
    position: absolute; inset: 0;
    background: linear-gradient(125deg, var(--card-back-a) 0%, #202022 50%, var(--card-back-b) 100%);
  }
  .back-brand {
    position: absolute;
    right: 34px;
    bottom: 28px;
    display: flex;
    align-items: center;
    gap: 5px;
  }
  .back-brand__dot { width: 8px; height: 8px; border-radius: 50%; background: var(--red); }
  .back-brand__name {
    font-weight: 800;
    font-size: 9px;
    color: var(--white);
    text-transform: uppercase;
  }
</style>
</head>
<body>
  <section class="card card--front">
    <div class="brand">
      <span class="brand__dot"></span>
      <span class="brand__name">Beacon Hazard Co.</span>
    </div>

    <svg class="divider" viewBox="0 0 525 256" aria-hidden="true">
      <line x1="258" y1="232" x2="298" y2="28" stroke="var(--gold)" stroke-width="1"/>
    </svg>

    <div class="identity">
      <p class="identity__name"><span class="identity__first">Lukas</span> <span class="identity__last">Varga</span></p>
      <p class="identity__role">Managing Director</p>
    </div>

    <ul class="contacts">
      <li class="contacts__item">
        <svg class="contacts__icon" viewBox="0 0 16 16" aria-hidden="true"><path d="M3.6 1.2 6 3.6 4.7 5.6c.9 2 2.6 3.8 4.7 4.7l2-1.3 2.4 2.4-1.6 2.6C7 13.6 2.4 9 1 3z"/></svg>
        (555) 204-3186
      </li>
      <li class="contacts__item">
        <svg class="contacts__icon" viewBox="0 0 16 16" aria-hidden="true"><path d="M1 3h14v10H1zM2.5 4.5 8 9l5.5-4.5z" fill-rule="evenodd"/></svg>
        hello@beaconhazard.co
      </li>
      <li class="contacts__item">
        <svg class="contacts__icon" viewBox="0 0 16 16" aria-hidden="true"><circle cx="8" cy="8" r="7"/><path d="M1 8h14M8 1c3 3.5 3 10.5 0 14M8 1c-3 3.5-3 10.5 0 14" stroke="var(--card)" stroke-width="1" fill="none"/></svg>
        www.beaconhazard.co
      </li>
    </ul>

    <div class="address-band">418 Linden Ave. Suite 300 Dallas, TX 75201</div>
  </section>

  <section class="card card--back">
    <div class="back-pattern" role="img" aria-label="Repeating tonal pattern of the company mark across the card back"></div>
    <div class="back-brand">
      <span class="back-brand__dot"></span>
      <span class="back-brand__name">Beacon Hazard Co.</span>
    </div>
  </section>
</body>
</html>
```